Meridale Staffing Website

My business has been word of mouth over the last 3 years and has grown. Now I need a website for additional marketing as we have new clients asking for a website.

You have already completed my Logo during an earlier project. I have attached the logo.

We do Staff Augmentation and Operation Support.

What is that?
Staff augmentation is an outsourcing strategy that allows companies to fill specific, temporary roles to achieve business objectives. This staffing method complements existing teams with specific talent, enhancing business capabilities or filling gaps left by members on extended leave.

We work alongside the internal recruiting team to assist clients to meet and exceed financial goals.

```html
<!DOCTYPE html>
<html lang="en">
<head>
<meta charset="utf-8">
<title>Meridale Staffing</title>
<link rel="stylesheet" href="https://fonts.googleapis.com/css2?family=Poppins:wght@400;500;600;700&family=Roboto:wght@400;500;700&display=swap">
<style>
:root{
  --navy:#173d66;
  --navy-deep:#0f2c4d;
  --accent:#2b6cb0;
  --ink:#1f2630;
  --muted:#5b6470;
  --grey:#eef0f3;
  --soft:#dfe4ea;
  --white:#ffffff;
  --photo-a:#7b8794;
  --photo-b:#c9ced4;
}
*{box-sizing:border-box;margin:0;padding:0}
html,body{width:1200px;height:4344px;overflow:hidden}
body{font-family:"Roboto",sans-serif;color:var(--ink);background:var(--white);position:relative}
h1,h2,h3,h4{font-family:"Poppins",sans-serif}
.abs{position:absolute}
.photo{background:linear-gradient(135deg,var(--photo-a),var(--photo-b))}
.btn{display:inline-block;border-radius:30px;font-family:"Poppins",sans-serif;font-weight:500;text-decoration:none}

/* header */
.site-header{position:absolute;left:0;top:0;width:1200px;height:80px;background:var(--white);display:flex;align-items:center;padding:0 112px}
.brand{display:flex;align-items:center;gap:10px;font-family:"Poppins",sans-serif;font-weight:600;font-size:20px;color:var(--navy)}
.brand-dot{width:34px;height:34px;border-radius:50%;background:var(--navy)}
.nav{display:flex;gap:42px;margin-left:auto;margin-right:40px;font-family:"Poppins",sans-serif;font-size:15px;font-weight:500}
.nav a{color:var(--ink);text-decoration:none}
.phone-pill{background:var(--navy-deep);color:var(--white);border-radius:24px;padding:9px 20px;font-size:15px;font-weight:500;display:flex;align-items:center;gap:8px}

/* hero */
.hero{left:0;top:80px;width:1200px;height:680px;overflow:hidden}
.hero-photo{position:absolute;inset:0;background:linear-gradient(100deg,#5c6a78 0%,#8e9aa6 45%,#b7a28c 75%,#6e7a86 100%)}
.hero-circle{position:absolute;left:30px;top:60px;width:360px;height:360px;border-radius:50%;background:var(--navy);border:8px solid var(--white);color:var(--white);text-align:center;padding:92px 24px 0}
.hero-circle h1{font-size:28px;line-height:1.2;font-weight:700}
.hero-circle p{font-size:13px;line-height:1.45;margin:12px 20px 22px;color:#dbe4ee}
.hero-circle .btn{background:var(--navy-deep);color:var(--white);padding:12px 28px;font-size:15px;border:1px solid #3a6290}
.hero-wave{position:absolute;left:0;bottom:0;width:1200px;height:200px}

/* about */
.about-title{left:112px;top:870px;font-size:40px;font-weight:500;color:var(--ink)}
.about-title span,.section-title span{color:var(--accent)}
.about-text{left:112px;top:950px;width:560px;font-size:15px;line-height:1.75;color:var(--muted)}
.about-btn{left:112px;top:1104px;background:var(--navy-deep);color:var(--white);padding:15px 32px;font-size:17px}
.about-backdrop{left:700px;top:730px;width:460px;height:460px;border-radius:50%;background:linear-gradient(135deg,var(--soft),#f3f5f8)}
.about-photo{left:760px;top:790px;width:340px;height:340px;border-radius:50%}

/* services */
.services{left:0;top:1248px;width:1200px;height:692px;background:linear-gradient(180deg,#1d4a78,#143a62)}
.section-title{width:1200px;text-align:center;font-size:40px;font-weight:500;color:var(--ink)}
.services .section-title{top:70px;color:var(--white)}
.services-intro{left:250px;top:150px;width:700px;text-align:center;font-size:14px;line-height:1.6;color:#d5dfea}
.service-card{top:250px;width:480px;height:360px;background:var(--grey);display:flex;overflow:hidden;border:1px solid #dfe3e8}
.service-body{width:232px;padding:26px 18px}
.service-body h3{font-size:17px;font-weight:600;color:var(--ink);margin-bottom:14px;white-space:nowrap}
.service-body p{font-size:13.5px;line-height:1.65;color:var(--muted)}
.service-body a{display:block;margin-top:26px;font-size:14px;color:var(--ink);font-weight:500}
.service-photo{flex:1}

/* testimonials */
.testi-title{top:2008px}
.testi-photo{left:112px;top:2112px;width:460px;height:410px}
.testi-card{left:552px;top:2120px;width:536px;height:400px;background:#f3f4f6;border-radius:10px;box-shadow:0 4px 14px rgba(0,0,0,.12);padding:30px 36px}
.testi-card h3{font-size:22px;font-weight:600;color:var(--navy);margin-bottom:14px}
.testi-card p{font-size:14.5px;line-height:1.75;color:var(--muted)}
.testi-card .author{margin-top:20px;font-weight:700;color:var(--ink);font-size:15px}
.testi-mark{position:absolute;right:26px;top:22px;width:28px;height:28px;border-radius:50%;background:var(--navy)}
.arrow-btn{width:42px;height:42px;border-radius:50%;background:#111;display:flex;align-items:center;justify-content:center}

/* cta */
.cta{left:0;top:2620px;width:1200px;height:480px;background:var(--navy);overflow:hidden}
.cta-photo{position:absolute;left:580px;top:0;width:700px;height:480px;border-radius:60% 0 0 50% / 70% 0 0 60%;border-left:14px solid var(--white)}
.cta-text{left:112px;top:90px;width:480px;color:var(--white);font-family:"Poppins",sans-serif;font-size:38px;font-weight:500;line-height:1.4;text-transform:uppercase}
.cta-btn{left:112px;top:360px;background:var(--white);color:var(--ink);padding:14px 26px;font-size:15px}

/* news */
.news-title{top:3168px}
.news-intro{left:250px;top:3250px;width:700px;text-align:center;font-size:14px;line-height:1.6;color:var(--muted)}
.news-card{top:3340px;height:420px;background:var(--white);border-radius:8px;box-shadow:0 3px 12px rgba(0,0,0,.14);overflow:hidden;text-align:center}
.news-photo{height:220px}
.news-card h3{font-size:18px;font-weight:600;margin:22px 16px 10px}
.news-card p{font-size:12.5px;line-height:1.6;color:var(--muted);padding:0 26px}
.news-card .btn{background:var(--navy-deep);color:var(--white);padding:8px 20px;font-size:11px;margin-top:18px}

/* footer */
.footer{left:0;top:3820px;width:1200px;height:524px;background:var(--navy);overflow:hidden}
.footer-wave{position:absolute;left:0;top:0;width:1200px;height:90px}
.footer .brand{position:absolute;left:112px;top:120px;color:var(--white);font-size:28px}
.footer .brand-dot{background:var(--white);width:44px;height:44px}
.footer-about{left:112px;top:200px;width:300px;font-size:12.5px;line-height:1.6;color:#c9d5e3}
.socials{left:112px;top:300px;display:flex;gap:12px}
.socials span{width:30px;height:30px;border-radius:50%;border:2px solid var(--white)}
.footer-col{top:130px;color:var(--white)}
.footer-col h4{font-size:17px;font-weight:600;margin-bottom:16px}
.footer-col ul{list-style:none}
.footer-col li{font-size:13px;margin-bottom:14px;color:#dbe4ee;display:flex;align-items:center;gap:8px}
.footer-col li::before{content:"";width:6px;height:6px;border-radius:50%;background:#9fb5cc}
.contact-list li::before{display:none}
.copyright{left:0;top:460px;width:1200px;height:64px;background:var(--navy-deep);color:#dbe4ee;font-size:13px;display:flex;align-items:center;justify-content:center}
</style>
</head>
<body>

<header class="site-header">
  <div class="brand"><span class="brand-dot"></span>Meridale Staffing</div>
  <nav class="nav"><a href="#">Home</a><a href="#">About</a><a href="#">Solution</a><a href="#">Testimonials</a><a href="#">Contact</a></nav>
  <div class="phone-pill">
    <svg width="14" height="14" viewBox="0 0 24 24"><path fill="#fff" d="M6.6 10.8a15 15 0 0 0 6.6 6.6l2.2-2.2c.3-.3.7-.4 1-.2 1.1.4 2.3.6 3.6.6.6 0 1 .4 1 1V20c0 .6-.4 1-1 1A17 17 0 0 1 3 4c0-.6.4-1 1-1h3.5c.6 0 1 .4 1 1 0 1.3.2 2.5.6 3.6.1.3 0 .7-.2 1z"/></svg>
    +1 555-014-2270
  </div>
</header>

<section class="abs hero">
  <div class="hero-photo" role="img" aria-label="Two colleagues smiling while reviewing a tablet in a bright office"></div>
  <div class="hero-circle">
    <h1>Welcome to<br>Meridale Staffing</h1>
    <p>We place skilled people beside your team so projects keep moving and goals stay in reach.</p>
    <a class="btn" href="#">Get Started</a>
  </div>
  <svg class="hero-wave" viewBox="0 0 1200 200" preserveAspectRatio="none">
    <path d="M0 120 C300 40 520 200 800 150 C980 118 1100 60 1200 70 L1200 200 L0 200Z" fill="#fff"/>
    <path d="M0 120 C300 40 520 200 800 150 C980 118 1100 60 1200 70" fill="none" stroke="#173d66" stroke-width="10"/>
  </svg>
</section>

<h2 class="abs about-title">About <span>Meridale Staffing</span></h2>
<p class="abs about-text">Meridale Staffing has grown by word of mouth for three years. We work alongside internal recruiting teams to fill specific, temporary roles and help clients meet and exceed their financial goals. Our people join quickly, learn your systems and leave your team stronger than before. From short projects to extended leave cover, we match talent to the need and stay close until the work is done.</p>
<a class="abs btn about-btn" href="#">Read More</a>
<div class="abs about-backdrop" role="img" aria-label="Soft grey curved decorative frame around the team image"></div>
<div class="abs about-photo photo" role="img" aria-label="Team members meeting around a laptop"></div>

<section class="abs services">
  <h2 class="abs section-title">Our Service</h2>
  <p class="abs services-intro">We support growing companies with flexible talent and steady operations, so your core team can stay focused on the work that matters most.</p>
  <article class="abs service-card" style="left:112px">
    <div class="service-body">
      <h3>Staff Augmentation</h3>
      <p>Fill specific, temporary roles with proven talent that complements your existing team and closes gaps left by extended leave.</p>
      <a href="#">Read More</a>
    </div>
    <div class="service-photo photo" role="img" aria-label="Support specialist wearing a headset"></div>
  </article>
  <article class="abs service-card" style="left:608px">
    <div class="service-body">
      <h3>Operation Support</h3>
      <p>Keep daily operations running smoothly with support staff who handle process, reporting and coordination while you grow.</p>
      <a href="#">Read More</a>
    </div>
    <div class="service-photo photo" role="img" aria-label="Colleague working at a desk in an office"></div>
  </article>
</section>

<h2 class="abs section-title testi-title">What <span>Customer Say</span></h2>
<div class="abs testi-photo photo" role="img" aria-label="Group of professionals standing together"></div>
<div class="abs testi-card">
  <span class="testi-mark"></span>
  <h3>Testimonials</h3>
  <p>"Meridale found the right people for us within days. They understood our goals, worked closely with our recruiters and filled every gap left by extended leave. Our projects stayed on schedule and our team felt supported from the very first week. I would recommend them to any company that needs skilled help fast."</p>
  <p class="author">- Dana Whitlock</p>
</div>
<div class="abs arrow-btn" style="left:1124px;top:2300px"><svg width="16" height="16" viewBox="0 0 16 16"><path d="M5 2l6 6-6 6" fill="none" stroke="#fff" stroke-width="2.4"/></svg></div>

<section class="abs cta">
  <div class="cta-photo photo" role="img" aria-label="Colleagues discussing plans in a modern office"></div>
  <p class="abs cta-text">Schedule a free consulation with a trusted advisor today!</p>
  <a class="abs btn cta-btn" href="#">Get a Free Quote</a>
</section>

<h2 class="abs section-title news-title">Latest <span>News</span></h2>
<p class="abs news-intro">Read the latest thinking on staffing, team growth and operations support from the Meridale Staffing team.</p>
<div class="abs arrow-btn" style="left:30px;top:3530px;background:#555"><svg width="16" height="16" viewBox="0 0 16 16"><path d="M11 2l-6 6 6 6" fill="none" stroke="#fff" stroke-width="2.4"/></svg></div>
<article class="abs news-card" style="left:112px;width:308px">
  <div class="news-photo photo" role="img" aria-label="Business team in a meeting"></div>
  <h3>Finibus Bonorum Malorum</h3>
  <p>Short notes on how flexible staffing keeps projects moving and budgets on track.</p>
  <a class="btn" href="#">READ MORE</a>
</article>
<article class="abs news-card" style="left:440px;width:312px">
  <div class="news-photo photo" role="img" aria-label="Professional smiling in an office"></div>
  <h3>Eiusmod Tempor Incididunt</h3>
  <p>How operation support frees leaders to focus on clients and long term growth.</p>
  <a class="btn" href="#">READ MORE</a>
</article>
<article class="abs news-card" style="left:772px;width:316px">
  <div class="news-photo photo" role="img" aria-label="Team talking in a glass meeting room"></div>
  <h3>Eiusmod Tempor Incididunt</h3>
  <p>Simple steps to bring augmented staff up to speed in their very first week.</p>
  <a class="btn" href="#">READ MORE</a>
</article>
<div class="abs arrow-btn" style="left:1128px;top:3530px"><svg width="16" height="16" viewBox="0 0 16 16"><path d="M5 2l6 6-6 6" fill="none" stroke="#fff" stroke-width="2.4"/></svg></div>

<footer class="abs footer">
  <svg class="footer-wave" viewBox="0 0 1200 90" preserveAspectRatio="none">
    <path d="M0 0 L1200 0 L1200 30 C900 90 400 10 0 60Z" fill="#fff"/>
    <path d="M0 60 C400 10 900 90 1200 30" fill="none" stroke="#6b86a6" stroke-width="6"/>
  </svg>
  <div class="brand"><span class="brand-dot"></span>Meridale Staffing</div>
  <p class="abs footer-about">Meridale Staffing is a staff augmentation and operation support partner helping companies fill roles and reach their goals.</p>
  <div class="abs socials"><span></span><span></span><span></span></div>
  <div class="abs footer-col" style="left:500px"><h4>Quick Links</h4><ul><li>Home</li><li>About</li><li>Services</li><li>Blog</li><li>Contact</li></ul></div>
  <div class="abs footer-col" style="left:680px"><h4>Help Links</h4><ul><li>FAQ</li><li>Terms</li><li>Privacy</li><li>Support</li><li>Conditions</li></ul></div>
  <div class="abs footer-col" style="left:870px"><h4>Contact us</h4>
    <ul class="contact-list">
      <li><svg width="14" height="14" viewBox="0 0 24 24"><path fill="#fff" d="M12 2a7 7 0 0 0-7 7c0 5 7 13 7 13s7-8 7-13a7 7 0 0 0-7-7zm0 9.5a2.5 2.5 0 1 1 0-5 2.5 2.5 0 0 1 0 5z"/></svg>12 Harbor Lane, Albany, NY</li>
      <li><svg width="14" height="14" viewBox="0 0 24 24"><path fill="#fff" d="M3 5h18v14H3z M3 5l9 7 9-7" stroke="#173d66" stroke-width="1.5"/></svg>hello@meridalestaffing.com</li>
      <li><svg width="14" height="14" viewBox="0 0 24 24"><path fill="#fff" d="M6.6 10.8a15 15 0 0 0 6.6 6.6l2.2-2.2c.3-.3.7-.4 1-.2 1.1.4 2.3.6 3.6.6.6 0 1 .4 1 1V20c0 .6-.4 1-1 1A17 17 0 0 1 3 4c0-.6.4-1 1-1h3.5c.6 0 1 .4 1 1 0 1.3.2 2.5.6 3.6.1.3 0 .7-.2 1z"/></svg>+1 555-014-2270</li>
    </ul>
  </div>
  <div class="abs copyright">Copyright@2023 All Rights Reserved</div>
</footer>

</body>
</html>
```